I need a logo that demonstrates multiple of the same with one of a distinguishing feature. I would like something that can be recognisable in silhouette format. The business designs Management systems bespoke the to the company helping them pre-qualify for work.
Something that can demonstrate a distinction between a collective group non of which are the same in shape or size, with the largest of these not the distinguished object (or something to that effect).
This is a new business no logo or artwork exists.
Target Market(s)
Small to Medium Size enterprises in the city and rural areas. Looking to make the step up.
Industry/Entity Type
Manufacture
Contact Information for Business Card
room for, Name, Email, phone number
Font styles to use
Requirements
Must have
- would like the silhouette to be recognisable
Nice to have
- would like it to incorporate the name Keystone Advisory Frameworks.
- Would like the same logo to be on both business cards and on corporate shirts
Should not have
- anything that may exclude rural trade or manufacturing.
- I don't want to appear as corporate, just professional

```html
<!DOCTYPE html>
<html lang="en">
<head>
<meta charset="utf-8">
<title>Keystone Advisory Frameworks – Business Card</title>
<link rel="stylesheet" href="https://fonts.googleapis.com/css2?family=Open+Sans:wght@300;400;600&display=swap">
<style>
  :root {
    --backdrop: #ecebe8;
    --card-white: #ffffff;
    --brand-orange: #f37021;
    --brand-red: #e2231a;
    --rule-orange: #f68a4a;
    --text-white: #ffffff;
  }
  * { margin: 0; padding: 0; box-sizing: border-box; }
  html, body {
    width: 1200px; height: 900px; overflow: hidden;
    background: var(--backdrop);
    font-family: "Open Sans", Arial, sans-serif;
  }
  .canvas { position: relative; width: 1200px; height: 900px; }

  .card {
    position: absolute;
    background: var(--card-white);
    box-shadow: 0 6px 18px rgba(0,0,0,0.12);
    overflow: hidden;
  }

  /* Front */
  .card-front { left: 77px; top: 34px; width: 589px; height: 364px; }
  .brand-header {
    position: absolute; left: 0; top: 0; width: 100%; height: 156px;
    display: flex; align-items: center; gap: 18px; padding-left: 33px;
  }
  .brand-dot {
    width: 62px; height: 62px; border-radius: 50%;
    border: 4px solid var(--brand-orange); flex: none;
  }
  .brand-name { color: var(--brand-red); font-weight: 400; line-height: 1.1; }
  .brand-name .line-main { display: block; font-size: 38px; letter-spacing: 1px; }
  .brand-name .line-sub { display: block; font-size: 17px; letter-spacing: 2.4px; }

  .contact-band {
    position: absolute; left: 0; top: 156px; width: 100%; height: 208px;
    background: var(--brand-orange); color: var(--text-white);
  }
  .person-name {
    position: absolute; left: 31px; top: 16px;
    font-size: 19px; font-weight: 600;
  }
  .person-role {
    position: absolute; left: 31px; top: 43px;
    font-size: 14.5px; font-weight: 400;
  }
  .contact-list { position: absolute; left: 0; top: 98px; width: 249px; list-style: none; }
  .contact-item {
    height: 31px; display: flex; align-items: center; gap: 10px;
    padding-left: 35px; font-size: 15px;
  }
  .contact-item + .contact-item { border-top: 1px solid var(--rule-orange); }
  .contact-icon { width: 13px; height: 13px; flex: none; fill: var(--text-white); }

  /* Back */
  .card-back { left: 388px; top: 505px; width: 567px; height: 352px; }
  .back-band {
    position: absolute; left: 0; top: 110px; width: 100%; height: 131px;
    background: var(--brand-orange);
    display: flex; align-items: center; justify-content: center;
  }
  .back-wordmark {
    color: var(--text-white); font-weight: 300; text-align: center; line-height: 1.05;
  }
  .back-wordmark .line-main { display: block; font-size: 44px; letter-spacing: 1px; }
  .back-wordmark .line-sub { display: block; font-size: 24px; letter-spacing: 2px; }
</style>
</head>
<body>
<div class="canvas">

  <section class="card card-front" aria-label="Business card front">
    <header class="brand-header">
      <span class="brand-dot"></span>
      <div class="brand-name">
        <span class="line-main">KEYSTONE</span>
        <span class="line-sub">ADVISORY FRAMEWORKS</span>
      </div>
    </header>
    <div class="contact-band">
      <p class="person-name">Daniel Harper</p>
      <p class="person-role">Managing Director</p>
      <ul class="contact-list">
        <li class="contact-item">
          <svg class="contact-icon" viewBox="0 0 24 24"><path d="M6.6 10.8a15 15 0 0 0 6.6 6.6l2.2-2.2c.3-.3.7-.4 1-.2 1.1.4 2.3.6 3.6.6.6 0 1 .4 1 1V20c0 .6-.4 1-1 1A17 17 0 0 1 3 4c0-.6.4-1 1-1h3.5c.6 0 1 .4 1 1 0 1.3.2 2.5.6 3.6.1.3 0 .7-.2 1z"/></svg>
          044-987 654 321
        </li>
        <li class="contact-item">
          <svg class="contact-icon" viewBox="0 0 24 24"><path d="M2 5h20v14H2z M4 7v.5l8 5 8-5V7l-8 5z" fill-rule="evenodd"/></svg>
          hello@keystoneaf.com
        </li>
        <li class="contact-item">
          <svg class="contact-icon" viewBox="0 0 24 24" fill="none" stroke="#fff" stroke-width="2.4" stroke-linecap="round"><path d="M10 14a4 4 0 0 0 5.6 0l3.6-3.6a4 4 0 0 0-5.6-5.6L12 6.4"/><path d="M14 10a4 4 0 0 0-5.6 0l-3.6 3.6a4 4 0 0 0 5.6 5.6l1.6-1.6"/></svg>
          www.keystoneaf.com
        </li>
      </ul>
    </div>
  </section>

  <section class="card card-back" aria-label="Business card back">
    <div class="back-band">
      <div class="back-wordmark">
        <span class="line-main">KEYSTONE</span>
        <span class="line-sub">Advisory Frameworks</span>
      </div>
    </div>
  </section>

</div>
</body>
</html>
```